Existing Website Requiring new Pages

I have an existing word press website that was built using elementor.
Website: www.tallowcrestcare.com.au
I require the Vacancies page (https://www.tallowcrestcare.com.au/vacancies/) to be modified to display our new properties along with minor tweaks to how the information is presented.
The vacancies to be displayed are the exactly the same as those that are located on the homepage of QMR website (https://qmr.org.au/)
The new pages that link off the Vacancies tab will require custom design.
There are roughly 8 pages/properties to be incorporated. i wish for the design to be very similar to that displayed in the following link; https://www.polunda.com.au/vacancies/merrylands
Along with this the back end has not been updated for the last 3 years so it also requires some maintenance.
Website is in the disability industry and the custom pages will display information relative to Property Vacancies.
I have attached a ZIP file with some design guides, the information for each of the properties (which will need to be modified to show our business name Tallowcrest Care) and the example of how it is to look based off the Polunda website.
If you guys have any suggestions or ideas on how to make this more presentable or possible i'm open to your ideas.
Target Market(s)
People looking for SDA properties custom built for people with a disability
Industry/Entity Type
Disability
Coding
Coded - Design and coding required
Number of Pages Required
5+ page

```html
<!DOCTYPE html>
<html lang="en">
<head>
<meta charset="utf-8">
<title>Tallowcrest Care – SDA Vacancies</title>
<link href="https://fonts.googleapis.com/css2?family=Poppins:wght@300;400;500&display=swap" rel="stylesheet">
<style>
:root{
  --gold:#f9b800;
  --gold-text:#f5b400;
  --ink:#111111;
  --muted:#333333;
  --badge:#f8ab86;
  --white:#ffffff;
  --panel:rgba(120,120,120,.55);
}
*{box-sizing:border-box;margin:0;padding:0}
html,body{width:1200px;height:3054px;overflow:hidden}
body{font-family:'Poppins',sans-serif;color:var(--ink);background:var(--white);position:relative}
a{color:inherit;text-decoration:none}

.site-header{position:absolute;top:0;left:0;width:1200px;height:158px}
.nav{position:absolute;top:66px;font-size:18px;display:flex;gap:40px;text-transform:uppercase;letter-spacing:.2px}
.nav-left{left:45px}
.nav-right{right:45px}
.nav .active{color:var(--gold-text);display:flex;align-items:center;gap:12px}
.brand{position:absolute;left:50%;top:44px;transform:translateX(-50%);display:flex;flex-direction:column;align-items:center;gap:8px}
.brand-mark{width:44px;height:44px;border-radius:50%;background:#ec6aa8}
.brand-name{font-size:20px;font-weight:400;color:#4a4a4a;white-space:nowrap}

.hero{position:absolute;top:158px;left:0;width:1200px;height:577px;color:var(--white)}
.hero-photo{position:absolute;inset:0;background:linear-gradient(160deg,#1c2a3c 0%,#3b3025 45%,#6a4a2a 70%,#2a3320 100%)}
.hero-title{position:absolute;left:45px;top:85px;font-size:71px;font-weight:400;line-height:100px;white-space:nowrap}
.hero-title .accent{color:var(--gold-text);display:block}
.hero-sub{position:absolute;left:45px;top:290px;font-size:19px;line-height:29px}
.filter{position:absolute;top:440px;width:263px}
.filter label{display:block;font-size:17px;text-transform:uppercase;margin-bottom:9px}
.select{height:57px;border:2px solid var(--white);border-radius:4px;display:flex;align-items:center;justify-content:space-between;padding:0 16px;font-size:19px}
.btn-search{position:absolute;left:892px;top:474px;width:263px;height:57px;background:var(--gold);border-radius:4px;display:flex;align-items:center;justify-content:center;font-size:19px}

.pill{position:absolute;left:538px;top:779px;width:124px;height:36px;border-radius:18px;background:var(--gold);color:var(--white);font-size:13px;display:flex;align-items:center;justify-content:center}
.section-title{position:absolute;left:0;width:1200px;top:836px;text-align:center;font-size:45px;line-height:60px;font-weight:400;white-space:nowrap;letter-spacing:-.3px}

.card{position:absolute;width:357px}
.card-photo{height:254px;border-radius:6px;position:relative;overflow:hidden}
.dots{position:absolute;left:66px;top:216px;display:flex;gap:14px}
.dots span{width:16px;height:16px;border-radius:50%;border:2px solid var(--white)}
.dots span:first-child{background:var(--white)}
.card-head{display:flex;justify-content:space-between;align-items:center;margin-top:24px}
.card-head h3{font-size:24px;font-weight:400}
.badge{background:var(--badge);color:var(--white);font-size:12px;border-radius:4px;padding:3px 12px}
.card p{font-size:15px;margin-top:20px;color:var(--muted);white-space:nowrap;overflow:hidden;text-overflow:ellipsis}
.btn-more{display:inline-block;margin-top:14px;background:var(--gold);color:var(--white);font-size:17px;padding:7px 15px;border-radius:4px}

.contact-band{position:absolute;top:2225px;left:0;width:1200px;height:492px;background:linear-gradient(180deg,#c9c9c9 0%,#b7aca6 45%,#6e6255 80%,#3c352c 100%)}
.contact-card{position:absolute;left:75px;top:45px;width:1049px;height:356px;border-radius:26px;background:var(--panel)}
.contact-card h2{position:absolute;left:38px;top:48px;font-size:40px;font-weight:400;line-height:56px;color:var(--white)}
.contact-list{position:absolute;left:38px;top:180px;list-style:none;color:var(--white);font-size:17px}
.contact-list li{display:flex;align-items:center;gap:12px;height:37px}
.map{position:absolute;left:488px;top:46px;width:516px;height:310px;border-radius:22px;background:linear-gradient(135deg,#e9ecef,#dfe5dc 50%,#e8e4d8)}

.site-footer{position:absolute;top:2717px;left:0;width:1200px;height:337px}
.footer-brand{position:absolute;left:47px;top:44px;display:flex;align-items:center;gap:10px}
.footer-contact{position:absolute;left:45px;top:170px;list-style:none;font-size:17px}
.footer-contact li{display:flex;align-items:center;gap:12px;height:41px}
.footer-col{position:absolute;top:48px}
.footer-col h4{color:var(--gold-text);font-size:21px;font-weight:400;margin-bottom:18px}
.footer-col ul{list-style:none;font-size:17px;line-height:25px}
.footer-col li{margin-bottom:8px}
.socials{display:grid;grid-template-columns:repeat(3,38px);gap:8px}
.socials span{width:38px;height:38px;border-radius:50%}
</style>
</head>
<body>

<header class="site-header">
  <nav class="nav nav-left">
    <a href="#">Home</a><a href="#">About Us</a>
    <a href="#" class="active">What We Do
      <svg width="12" height="8" viewBox="0 0 12 8"><path d="M1 1l5 5 5-5" fill="none" stroke="#f5b400" stroke-width="2"/></svg></a>
  </nav>
  <div class="brand"><span class="brand-mark"></span><span class="brand-name">Tallowcrest Care</span></div>
  <nav class="nav nav-right">
    <a href="#">Referals</a><a href="#">Feedback</a><a href="#">Contact Us</a>
  </nav>
</header>

<section class="hero">
  <div class="hero-photo" role="img" aria-label="Illuminated timber suburban house at dusk among trees"></div>
  <h1 class="hero-title"><span class="accent">Next-generation</span>SDA Home</h1>
  <p class="hero-sub">Custom-built SDA apartments with families in mind.<br>Your new suburban home awaits.</p>
  <div class="filter" style="left:45px"><label>Current or Future</label><div class="select">Both<svg width="12" height="8" viewBox="0 0 12 8"><path d="M1 1l5 5 5-5" fill="none" stroke="#fff" stroke-width="2"/></svg></div></div>
  <div class="filter" style="left:327px"><label>Design Category</label><div class="select">All Categories<svg width="12" height="8" viewBox="0 0 12 8"><path d="M1 1l5 5 5-5" fill="none" stroke="#fff" stroke-width="2"/></svg></div></div>
  <div class="filter" style="left:610px"><label>Location</label><div class="select">All Suburbs<svg width="12" height="8" viewBox="0 0 12 8"><path d="M1 1l5 5 5-5" fill="none" stroke="#fff" stroke-width="2"/></svg></div></div>
  <a class="btn-search" href="#">Search</a>
</section>

<span class="pill">Our Properties</span>
<h2 class="section-title">View Our SDA Vacancies and Homes Being Built</h2>

<article class="card" style="left:45px;top:930px"><div class="card-photo" role="img" aria-label="Yellow weatherboard house with lawn" style="background:linear-gradient(180deg,#c9d6de,#d8b070 45%,#5f8a2c)"><div class="dots"><span></span><span></span><span></span><span></span><span></span><span></span><span></span><span></span></div></div><div class="card-head"><h3>Greystanes</h3><span class="badge">SDA</span></div><p>Fully accesible, High physical support</p><a class="btn-more" href="#">More details</a></article>

<article class="card" style="left:421px;top:930px"><div class="card-photo" role="img" aria-label="Cream cottage with grey roof under white sky" style="background:linear-gradient(180deg,#f3f4f6,#e8e4d2 50%,#7a8a5c)"><div class="dots"><span></span><span></span><span></span><span></span><span></span><span></span><span></span><span></span></div></div><div class="card-head"><h3>Jordan Springs</h3><span class="badge">SDA</span></div><p>Fully accesible, Improved liveability</p><a class="btn-more" href="#">More details</a></article>

<article class="card" style="left:797px;top:930px"><div class="card-photo" role="img" aria-label="Brick two-storey house with double garage" style="background:linear-gradient(180deg,#2a78d8,#9c6050 55%,#6a6a6a)"><div class="dots"><span></span><span></span><span></span><span></span><span></span><span></span><span></span><span></span></div></div><div class="card-head"><h3>Werrington</h3><span class="badge">SDA</span></div><p>Fully accesible, Improved liveability</p><a class="btn-more" href="#">More details</a></article>

<article class="card" style="left:45px;top:1353px"><div class="card-photo" role="img" aria-label="Modern white and timber house under cloudy sky" style="background:linear-gradient(180deg,#b9cde0,#e6e4e2 50%,#8d9a80)"><div class="dots"><span></span><span></span><span></span><span></span><span></span><span></span><span></span><span></span></div></div><div class="card-head"><h3>Wentworthville</h3><span class="badge">SDA</span></div><p>Fully accesible, High physical support, Improved liveability</p><a class="btn-more" href="#">More details</a></article>

<article class="card" style="left:421px;top:1353px"><div class="card-photo" role="img" aria-label="White house with red roof and garden" style="background:linear-gradient(180deg,#d04a52,#e8eaec 40%,#4f8a30)"><div class="dots"><span></span><span></span><span></span><span></span><span></span><span></span><span></span><span></span></div></div><div class="card-head"><h3>West Pennant Hills</h3><span class="badge">SDA</span></div><p>High physical support</p><a class="btn-more" href="#">More details</a></article>

<article class="card" style="left:797px;top:1353px"><div class="card-photo" role="img" aria-label="Thatched timber house on green lawn" style="background:linear-gradient(180deg,#8ab8e8,#8a6a4a 55%,#5b8d2c)"><div class="dots"><span></span><span></span><span></span><span></span><span></span><span></span><span></span><span></span></div></div><div class="card-head"><h3>Guildford West</h3><span class="badge">SDA</span></div><p>Fully accesible, High physical support</p><a class="btn-more" href="#">More details</a></article>

<article class="card" style="left:45px;top:1776px"><div class="card-photo" role="img" aria-label="Red brick house among green trees" style="background:linear-gradient(180deg,#4b92e0,#3f7a2a 45%,#8c4a38 65%,#4f8a2e)"><div class="dots"><span></span><span></span><span></span><span></span><span></span><span></span><span></span><span></span></div></div><div class="card-head"><h3>Austral</h3><span class="badge">SDA</span></div><p>Fully accesible, High physical support, Robust</p><a class="btn-more" href="#">More details</a></article>

<article class="card" style="left:421px;top:1776px"><div class="card-photo" role="img" aria-label="White house with porch among autumn trees" style="background:linear-gradient(180deg,#5a5a3a,#c07a2a 35%,#5a3a30 55%,#e8e6e0 75%,#4a6a30)"><div class="dots"><span></span><span></span><span></span><span></span><span></span><span></span><span></span><span></span></div></div><div class="card-head"><h3>Merrylands</h3><span class="badge">SDA</span></div><p>Fully accesible, High physical support</p><a class="btn-more" href="#">More details</a></article>

<article class="card" style="left:797px;top:1776px"><div class="card-photo" role="img" aria-label="Grey house with wrap-around white porch" style="background:linear-gradient(180deg,#a8c8e8,#8a96a0 45%,#e4e4e4 65%,#5b8c2e)"><div class="dots"><span></span><span></span><span></span><span></span><span></span><span></span><span></span><span></span></div></div><div class="card-head"><h3>Blacktown</h3><span class="badge">SDA</span></div><p>High physical support</p><a class="btn-more" href="#">More details</a></article>

<section class="contact-band" role="img" aria-label="Blurred red-roofed house on a hill">
  <div class="contact-card">
    <h2>For Some Questions,<br>Please Contact Us</h2>
    <ul class="contact-list">
      <li><svg width="18" height="14" viewBox="0 0 18 14"><rect x="1" y="1" width="16" height="12" fill="none" stroke="#fff" stroke-width="1.5"/><path d="M1 1l8 6 8-6" fill="none" stroke="#fff" stroke-width="1.5"/></svg>info@tallowcrestcare.com.au</li>
      <li><svg width="18" height="18" viewBox="0 0 24 24"><path d="M6.6 10.8a15 15 0 006.6 6.6l2.2-2.2a1 1 0 011-.25 11.4 11.4 0 003.6.6 1 1 0 011 1V20a1 1 0 01-1 1A17 17 0 013 4a1 1 0 011-1h3.5a1 1 0 011 1 11.4 11.4 0 00.6 3.6 1 1 0 01-.25 1z" fill="#fff"/></svg>+61 0400 318 262</li>
      <li><svg width="18" height="18" viewBox="0 0 18 18"><circle cx="9" cy="9" r="7.5" fill="none" stroke="#fff" stroke-width="1.5"/><path d="M9 4.5V9l3 2" fill="none" stroke="#fff" stroke-width="1.5"/></svg>9AM To 5PM Monday - Friday</li>
    </ul>
    <div class="map" role="img" aria-label="Street map of western Sydney suburbs around Merrylands"></div>
  </div>
</section>

<footer class="site-footer">
  <div class="footer-brand"><span class="brand-mark"></span><span class="brand-name">Tallowcrest Care</span></div>
  <ul class="footer-contact">
    <li><svg width="18" height="14" viewBox="0 0 18 14"><rect x="1" y="1" width="16" height="12" fill="none" stroke="#f5b400" stroke-width="1.5"/><path d="M1 1l8 6 8-6" fill="none" stroke="#f5b400" stroke-width="1.5"/></svg>info@tallowcrestcare.com.au</li>
    <li><svg width="18" height="18" viewBox="0 0 24 24"><path d="M6.6 10.8a15 15 0 006.6 6.6l2.2-2.2a1 1 0 011-.25 11.4 11.4 0 003.6.6 1 1 0 011 1V20a1 1 0 01-1 1A17 17 0 013 4a1 1 0 011-1h3.5a1 1 0 011 1 11.4 11.4 0 00.6 3.6 1 1 0 01-.25 1z" fill="#f5b400"/></svg>+61 0400 318 262</li>
    <li><svg width="18" height="18" viewBox="0 0 18 18"><circle cx="9" cy="9" r="7.5" fill="none" stroke="#f5b400" stroke-width="1.5"/><path d="M9 4.5V9l3 2" fill="none" stroke="#f5b400" stroke-width="1.5"/></svg>9AM To 5PM Monday - Friday</li>
  </ul>
  <div class="footer-col" style="left:499px;width:250px">
    <h4>ACCOMMODATION</h4>
    <ul><li>Supported Independent Living (SIL)</li><li>Specialist Disability Accommodation (SDA)</li><li>Short term Accommodation (Respite)</li><li>Vacansies</li></ul>
  </div>
  <div class="footer-col" style="left:773px;width:200px">
    <h4>WHAT WE DO</h4>
    <ul><li>In Home Care</li><li>Social &amp; Community Services</li><li>Therapeutic Supports</li><li>Support Coordination</li><li>Home Modifications</li></ul>
  </div>
  <div class="footer-col" style="left:993px">
    <h4>FOLLOW US ON</h4>
    <div class="socials"><span style="background:#c13584"></span><span style="background:#1877f2"></span><span style="background:#0a66c2"></span><span style="background:#6b2a7a"></span></div>
  </div>
</footer>

</body>
</html>
```